Business Card Design for Property Development Company Director

I am looking for a professional and unforgettable business card design for our Director of our Property Development Company.
Please see attached .pptx file to find out what information to include. You don't have to follow the exact format shown in the file - I am interested to see your creative flair using the information provided.

```html
<!DOCTYPE html>
<html lang="en">
<head>
<meta charset="utf-8">
<title>Norvale Property Group – Business Card</title>
<link href="https://fonts.googleapis.com/css2?family=Roboto:wght@400;500;700&family=Roboto+Condensed:wght@700&display=swap" rel="stylesheet">
<style>
  :root {
    --bg: #e4e5e7;
    --card: #f7f7f8;
    --blue: #274b97;
    --grey: #55575c;
    --grey-light: #6b6d72;
    --faint: #ececee;
    --white: #ffffff;
  }
  * { margin: 0; padding: 0; box-sizing: border-box; }
  html, body { width: 1200px; height: 726px; overflow: hidden; }
  body {
    background: var(--bg);
    font-family: "Roboto", Arial, sans-serif;
    position: relative;
  }
  .card {
    position: absolute;
    width: 530px;
    height: 310px;
    background: var(--card);
    border-radius: 3px;
    box-shadow: 0 2px 6px rgba(0,0,0,0.12);
    overflow: hidden;
  }
  .card--front { left: 45px; top: 80px; }
  .card--back { left: 625px; top: 336px; }

  /* Front */
  .tagline {
    position: absolute; top: 34px; left: 0; right: 0;
    text-align: center; color: var(--blue);
    font-size: 19px; line-height: 1.15; font-weight: 400;
  }
  .brand { position: absolute; display: flex; align-items: center; gap: 12px; z-index: 2; }
  .brand__mark { width: 46px; height: 46px; background: var(--grey); flex: none; }
  .brand__name { color: var(--grey); font-weight: 700; text-transform: uppercase; line-height: 1; }
  .brand__name span { display: block; }
  .card--front .brand { left: 100px; top: 104px; }
  .card--front .brand__name .main { font-size: 44px; letter-spacing: 1px; }
  .card--front .brand__name .sub { font-size: 17px; letter-spacing: 4.5px; margin-top: 3px; }
  .stripe { position: absolute; top: 182px; left: 0; right: 0; height: 8px; display: flex; }
  .stripe__grey { width: 48%; background: var(--grey); }
  .stripe__blue { flex: 1; background: var(--blue); }
  .ask {
    position: absolute; top: 206px; left: 0; right: 0; text-align: center;
    font-size: 15px; color: var(--grey);
  }
  .ask em { font-style: normal; color: var(--blue); text-transform: uppercase; }
  .front-foot { position: absolute; bottom: 0; left: 0; right: 0; height: 14px; display: flex; }
  .front-foot .stripe__grey { width: 30%; }

  /* Back */
  .back-decor { position: absolute; right: 22px; top: 16px; width: 120px; height: 120px; background: var(--faint); }
  .back-art { position: absolute; inset: 0; }
  .card--back .brand { left: 34px; top: 34px; }
  .card--back .brand__mark { width: 40px; height: 40px; }
  .card--back .brand__name .main { font-size: 36px; letter-spacing: 1px; }
  .card--back .brand__name .sub { font-size: 14px; letter-spacing: 3.8px; margin-top: 3px; }
  .licence { position: absolute; left: 34px; top: 104px; font-size: 14px; color: var(--grey); }
  .licence span { color: var(--blue); }
  .contacts { position: absolute; left: 34px; top: 144px; list-style: none; }
  .contacts li {
    display: flex; align-items: center; gap: 10px;
    font-size: 15px; color: var(--grey); line-height: 24px;
  }
  .contacts svg { width: 13px; height: 13px; fill: var(--blue); flex: none; }
  .person {
    position: absolute; right: 24px; top: 196px; text-align: right; color: var(--white);
    white-space: nowrap; z-index: 2;
  }
  .person__name { font-family: "Roboto Condensed", Arial, sans-serif; font-weight: 700; font-size: 20px; }
  .person__role { font-size: 12px; margin-top: 2px; }
</style>
</head>
<body>

<section class="card card--front">
  <p class="tagline">Property Development<br>&amp; Site Acquisition Specialists</p>
  <div class="brand">
    <div class="brand__mark"></div>
    <div class="brand__name"><span class="main">Norvale</span><span class="sub">Property Group</span></div>
  </div>
  <div class="stripe"><div class="stripe__grey"></div><div class="stripe__blue"></div></div>
  <p class="ask">Ask me about our <em>Investment &amp; Partnership</em> opportunities</p>
  <div class="front-foot"><div class="stripe__grey"></div></div>
</section>

<section class="card card--back">
  <div class="back-decor"></div>
  <svg class="back-art" viewBox="0 0 530 310" preserveAspectRatio="none" aria-hidden="true">
    <path d="M530,100 C440,110 400,150 370,200 C330,265 250,300 150,310 L530,310 Z" fill="var(--blue)"/>
    <path d="M530,82 C430,92 390,140 358,190 C318,255 240,292 140,302 C232,288 300,252 344,198 C384,146 430,100 530,92 Z" fill="var(--grey)"/>
    <path d="M110,310 C190,302 250,292 292,274 C252,298 200,308 140,310 Z" fill="var(--grey-light)"/>
  </svg>
  <div class="brand">
    <div class="brand__mark"></div>
    <div class="brand__name"><span class="main">Norvale</span><span class="sub">Property Group</span></div>
  </div>
  <p class="licence">Real Estate Lic: <span>4102583 &amp; 4102584</span></p>
  <ul class="contacts">
    <li><svg viewBox="0 0 16 16"><path d="M3 1l3 3-1.5 2a9 9 0 0 0 5.5 5.5L12 10l3 3-2 2C7 15 1 9 1 3z"/></svg>0400 123 456</li>
    <li><svg viewBox="0 0 16 16"><path d="M1 3h14v10H1z M1 3l7 6 7-6" stroke="var(--card)" stroke-width="1"/></svg>daniel@norvale.com.au</li>
    <li><svg viewBox="0 0 16 16"><circle cx="8" cy="8" r="7"/><path d="M1 8h14M8 1c-3 4-3 10 0 14M8 1c3 4 3 10 0 14" stroke="var(--card)" stroke-width="1" fill="none"/></svg>www.norvale.com.au</li>
  </ul>
  <div class="person">
    <p class="person__name">Daniel Mercer</p>
    <p class="person__role">Director</p>
  </div>
</section>

</body>
</html>
```